Tor BQX, Inc. Business Cards/Stationary
Business Cards/Stationary/Letterhead
Attention all:
email is hgalloway@navemorta.org
Sorry for the mistake…it doesn't detract from the excellent designs!
I will likely select a winner soon, within the next day or two…
Hank Galloway
Can you show me where the Name and Title would go on #1,#2,#3,#4…?
Also…on the back of the card…I love the map/Logo. Can we put the www.navemorta.org under it?
On numbers #1-#7 - is that a white background? Off-white? Soft gray? Silver? I really like it -- contrasts beautifully with the red, black, and blue...
TR/VKH/NE Team.

```html
<!DOCTYPE html>
<html lang="en">
<head>
<meta charset="utf-8">
<title>Tor BQX, Inc. — Stationery Concepts</title>
<link href="https://fonts.googleapis.com/css2?family=Libre+Baskerville:wght@700&family=Open+Sans:wght@400;600&display=swap" rel="stylesheet">
<style>
  :root{
    --backdrop:#3b2f29;
    --paper:#ffffff;
    --paper-shade:#f1f1f1;
    --ink:#1c1c1c;
    --ink-soft:#6b6b6b;
    --brand-red:#a3141a;
    --brand-black:#111111;
    --label:#d9d2cc;
  }
  *{box-sizing:border-box;margin:0;padding:0}
  html,body{width:1200px;height:466px;overflow:hidden;background:var(--backdrop)}
  body{position:relative;font-family:"Open Sans",sans-serif;color:var(--ink)}

  .label{position:absolute;font-size:7px;letter-spacing:1.4px;text-transform:uppercase;color:var(--label);font-weight:600}
  .label--section{font-size:8px;letter-spacing:2px}

  .sheet{position:absolute;background:var(--paper);overflow:hidden;box-shadow:0 2px 6px rgba(0,0,0,.35)}

  .brand-block{display:flex;flex-direction:column;align-items:flex-start}
  .brand{font-family:"Libre Baskerville",serif;font-weight:700;color:var(--ink);line-height:1.1;white-space:nowrap}
  .brand__tagline{font-family:"Open Sans",sans-serif;font-size:4px;line-height:5px;color:var(--ink-soft);letter-spacing:.6px;text-transform:uppercase;margin-top:3px;border-top:1px solid var(--brand-red);padding-top:1px}

  .contact{position:absolute;font-size:4.2px;color:var(--ink-soft);line-height:7px}
  .contact li{list-style:none;display:flex;align-items:center;gap:3px}
  .contact li::before{content:"";width:3px;height:3px;background:var(--brand-red);flex:none}

  .swoosh{position:absolute;left:0;bottom:0;width:100%;height:34px}

  /* business cards */
  .card{width:122px;height:62px;left:17px}
  .card--front{top:228px}
  .card--back{top:324px}
  .card .brand{position:absolute;left:8px;top:7px;font-size:10px}
  .card__person{position:absolute;left:8px;top:24px;font-size:4.4px;line-height:5.6px;color:var(--ink-soft)}
  .card__person strong{font-weight:600;color:var(--ink)}
  .card--back .brand{left:0;right:0;top:16px;text-align:center;font-size:12px}
  .card__web{position:absolute;left:0;right:0;top:34px;text-align:center;font-size:4.6px;color:var(--ink-soft)}

  /* letterheads */
  .letterhead{width:276px;height:393px;top:29px}
  .letterhead--one{left:180px}
  .letterhead--two{left:485px}
  .letterhead .brand-block{position:absolute;left:16px;top:14px}
  .letterhead .brand{font-size:15px}
  .letterhead .contact{left:186px;top:14px}
  .letterhead__footer{position:absolute;left:0;right:0;bottom:10px;text-align:center;font-size:4.2px;color:var(--paper);z-index:2}

  /* envelopes */
  .flap{position:absolute;left:797px;width:384px}
  .flap svg{display:block;width:100%;height:100%}
  .flap--black{top:24px;height:80px}
  .flap--red{top:115px;height:84px}
  .flap--white{top:211px;height:74px}
  .envelope{left:797px;top:300px;width:384px;height:120px}
  .envelope .brand-block{position:absolute;left:14px;top:12px}
  .envelope .brand{font-size:13px}
  .envelope__address{position:absolute;left:14px;top:44px;font-size:4.4px;line-height:6.5px;color:var(--ink-soft)}
  .envelope .swoosh{height:20px}
</style>
</head>
<body>

<span class="label label--section" style="left:38px;top:172px">Stationery Concepts</span>

<section class="sheet card card--front">
  <div class="brand">Tor BQX<span style="font-size:5px">, Inc.</span></div>
  <div class="card__person"><strong>Hank Galloway</strong><br>Director<br>Phone 555-0142<br>hgalloway@navemorta.org</div>
  <svg class="swoosh" viewBox="0 0 122 14" preserveAspectRatio="none" style="height:8px">
    <path d="M0 8 Q61 -2 122 8 L122 14 L0 14Z" fill="var(--brand-black)"/>
    <path d="M0 7 Q61 -3 122 7" fill="none" stroke="var(--brand-red)" stroke-width="1.2"/>
  </svg>
</section>
<span class="label" style="left:40px;top:296px">Business Card Front</span>

<section class="sheet card card--back">
  <div class="brand">Tor BQX, Inc.</div>
  <div class="card__web">www.navemorta.org</div>
  <svg class="swoosh" viewBox="0 0 122 14" preserveAspectRatio="none" style="height:8px">
    <path d="M0 8 Q61 -2 122 8 L122 14 L0 14Z" fill="var(--brand-black)"/>
    <path d="M0 7 Q61 -3 122 7" fill="none" stroke="var(--brand-red)" stroke-width="1.2"/>
  </svg>
</section>
<span class="label" style="left:42px;top:394px">Business Card Back</span>

<section class="sheet letterhead letterhead--one">
  <div class="brand-block">
    <div class="brand">Tor BQX<span style="font-size:7px">, Inc.</span></div>
    <div class="brand__tagline">Relocation Services</div>
  </div>
  <ul class="contact">
    <li>120 Harbor Lane, Suite 4</li>
    <li>Phone 555-0142</li>
    <li>hgalloway@navemorta.org</li>
    <li>www.navemorta.org</li>
  </ul>
  <svg class="swoosh" viewBox="0 0 276 34" preserveAspectRatio="none">
    <path d="M0 22 Q138 4 276 22 L276 34 L0 34Z" fill="var(--brand-black)"/>
    <path d="M0 20 Q138 2 276 20" fill="none" stroke="var(--brand-red)" stroke-width="1.6"/>
  </svg>
</section>
<span class="label" style="left:282px;top:430px">Letter Head Option 1</span>

<section class="sheet letterhead letterhead--two">
  <div class="brand-block">
    <div class="brand">Tor BQX<span style="font-size:7px">, Inc.</span></div>
    <div class="brand__tagline">Relocation Services</div>
  </div>
  <svg class="swoosh" viewBox="0 0 276 34" preserveAspectRatio="none">
    <path d="M0 22 Q138 4 276 22 L276 34 L0 34Z" fill="var(--brand-black)"/>
    <path d="M0 20 Q138 2 276 20" fill="none" stroke="var(--brand-red)" stroke-width="1.6"/>
  </svg>
  <p class="letterhead__footer">120 Harbor Lane, Suite 4 &nbsp;|&nbsp; Phone 555-0142 &nbsp;|&nbsp; hgalloway@navemorta.org &nbsp;|&nbsp; www.navemorta.org</p>
</section>
<span class="label" style="left:586px;top:430px">Letter Head Option 2</span>

<div class="flap flap--black">
  <svg viewBox="0 0 384 80" preserveAspectRatio="none"><path d="M0 0H384V40L340 80H44L0 40Z" fill="var(--brand-black)"/></svg>
</div>
<div class="flap flap--red">
  <svg viewBox="0 0 384 84" preserveAspectRatio="none"><path d="M0 0H384V42L340 84H44L0 42Z" fill="var(--brand-red)"/></svg>
</div>
<div class="flap flap--white">
  <svg viewBox="0 0 384 74" preserveAspectRatio="none"><path d="M0 0H384V36L340 74H44L0 36Z" fill="var(--paper)"/><path d="M0 36L44 74H340L384 36" fill="none" stroke="#d6d6d6" stroke-width="1"/></svg>
</div>

<section class="sheet envelope">
  <div class="brand-block">
    <div class="brand">Tor BQX<span style="font-size:6px">, Inc.</span></div>
    <div class="brand__tagline">Relocation Services</div>
  </div>
  <p class="envelope__address">120 Harbor Lane, Suite 4<br>Portside, VA 20000</p>
  <svg class="swoosh" viewBox="0 0 384 20" preserveAspectRatio="none">
    <path d="M0 13 Q192 2 384 13 L384 20 L0 20Z" fill="var(--brand-black)"/>
    <path d="M0 12 Q192 1 384 12" fill="none" stroke="var(--brand-red)" stroke-width="1.4"/>
  </svg>
</section>
<span class="label" style="left:960px;top:430px">Envelope Option</span>

</body>
</html>
```